Business card por a urban DJ, up scale audience target

Need a sober design, modern, conservative colors but i can consider some options, y play rnb, hip hop, EDM and top40.

Business card for contact and personal info, double sided, use logo attrached please; im 42 so i need a card acording to my age an target audience.

Target Market(s)

Adult people, up scale audience

Industry/Entity Type

Music Download

Contact Information for Business Card

Cel (318) 4207265518 www.lumadrift.com

Requirements
Must have
• open mind
Nice to have
• open mind
Should not have
• DJ

```html
<!DOCTYPE html>
<html lang="en">
<head>
<meta charset="utf-8">
<title>LUMA Business Card</title>
<link rel="stylesheet" href="https://fonts.googleapis.com/css2?family=Open+Sans:wght@400;600;800&display=swap">
<style>
  :root {
    --backdrop: #e9e6e1;
    --card: #2b2b2b;
    --mark: #d4d5d7;
    --text: #cfcfcf;
    --text-strong: #bdbdbd;
  }
  * { margin: 0; padding: 0; box-sizing: border-box; }
  html, body {
    width: 1200px; height: 900px; overflow: hidden;
    background: var(--backdrop);
    font-family: "Open Sans", sans-serif;
  }
  .sheet { position: relative; width: 1200px; height: 900px; }
  .card {
    position: absolute; left: 320px;
    width: 560px; height: 320px;
    background: var(--card);
    box-shadow: 0 8px 24px rgba(0,0,0,0.18);
  }
  .card--front { top: 80px; }
  .card--back  { top: 500px; }
  .brand-name {
    position: absolute;
    font-weight: 800; color: var(--mark);
    letter-spacing: 2px; line-height: 1;
  }
  .card--front .brand-name {
    left: 0; right: 0; top: 122px;
    text-align: center; font-size: 78px;
  }
  .card--back .brand-name {
    left: 56px; top: 208px; font-size: 64px;
  }
  .contact {
    position: absolute; left: 330px; top: 38px;
    color: var(--text); font-size: 11.5px; line-height: 1.4;
  }
  .contact__name { font-size: 16px; font-weight: 600; color: var(--text-strong); line-height: 1.2; }
  .contact__role { font-size: 11px; margin-bottom: 12px; }
  .contact__address { margin-bottom: 14px; }
  .contact__list { list-style: none; }
  .contact__list li { display: flex; align-items: center; gap: 9px; }
  .contact__list svg { width: 10px; height: 10px; fill: var(--text); flex: none; }
</style>
</head>
<body>
<main class="sheet">
  <section class="card card--front" aria-label="Card front">
    <div class="brand-name">LUMA</div>
  </section>

  <section class="card card--back" aria-label="Card back">
    <div class="contact">
      <p class="contact__name">Marcus Reyes</p>
      <p class="contact__role">Managing Director</p>
      <p class="contact__address">12345, Address Goes Here<br>Country Name, 123456.</p>
      <ul class="contact__list">
        <li>
          <svg viewBox="0 0 10 10" aria-hidden="true"><path d="M2 0.5 L3.6 2.6 L2.8 3.6 Q3.8 5.8 6.4 7.2 L7.4 6.4 L9.5 8 L8.4 9.5 Q4.6 9.4 2 6.8 Q0.4 4.6 0.5 1.6 Z"/></svg>
          <span>(318) 4207265518</span>
        </li>
        <li>
          <svg viewBox="0 0 10 10" aria-hidden="true"><path d="M0.5 2 H9.5 V8 H0.5 Z M1.2 2.6 L5 5.5 L8.8 2.6 Z" fill-rule="evenodd"/></svg>
          <span>info@lumadrift.com</span>
        </li>
        <li>
          <svg viewBox="0 0 10 10" aria-hidden="true"><path d="M4 6 L6 4 M3.2 4.6 L1.6 6.2 A1.5 1.5 0 0 0 3.8 8.4 L5.4 6.8 M6.8 5.4 L8.4 3.8 A1.5 1.5 0 0 0 6.2 1.6 L4.6 3.2" stroke="#cfcfcf" stroke-width="1.2" fill="none"/></svg>
          <span>www.lumadrift.com</span>
        </li>
      </ul>
    </div>
    <div class="brand-name">LUMA</div>
  </section>
</main>
</body>
</html>
```